Verdana Crest New Website - Online Learning and Education

New Wordpress website for an online learning site that has courses, worksheets, quizzes, etc.
Updates

We would like something similar to this website: https://hallowaybridgeinstitute.example/mediation-skills-course/. But continue with the content of our current website: http://verdanacrestlearninghub.example

We would like something similar to this site: https://hallowaybridgeinstitute.example/mediation-skills-course/

Coding

Coded - Design and coding required

```html
<!DOCTYPE html>
<html lang="en">
<head>
<meta charset="utf-8">
<title>Verdana Crest Learning System</title>
<link href="https://fonts.googleapis.com/css2?family=Lato:wght@400;700;900&family=Open+Sans:wght@400;600&display=swap" rel="stylesheet">
<style>
:root{
  --navy:#1d4a82;
  --navy-deep:#0c2a50;
  --navy-darker:#081f3d;
  --red:#c1202f;
  --text:#3a3a3a;
  --link:#1f5496;
  --white:#ffffff;
}
*{margin:0;padding:0;box-sizing:border-box}
html,body{width:1200px;height:2961px;overflow:hidden}
body{position:relative;background:var(--white);font-family:"Open Sans",sans-serif;color:var(--text)}
.abs{position:absolute}
.heading{font-family:"Lato",sans-serif;font-weight:700;text-transform:uppercase}

/* header */
.site-header{left:0;top:0;width:1200px;height:99px;background:var(--white)}
.brand{left:161px;top:33px;display:flex;align-items:center;gap:9px;font-family:"Lato",sans-serif;font-weight:700;font-size:26px;color:var(--navy)}
.brand-dot{width:24px;height:24px;border-radius:50%;background:var(--navy)}
.main-nav{left:464px;top:41px;display:flex;gap:27px;font-family:"Lato",sans-serif;font-weight:700;font-size:15.5px;color:#4a4a4a}

/* hero */
.hero{left:0;top:99px;width:1200px;height:461px;background:linear-gradient(90deg,#f4f3f0 0%,#eeebe5 45%,#c9c3ba 70%,#a9a39c 100%)}
.hero-title{left:167px;top:232px;font-size:35px;font-weight:900;color:var(--navy)}
.hero-sub{left:167px;top:286px;font-family:"Lato",sans-serif;font-size:22px;color:#333}
.btn-launch{left:168px;top:336px;width:184px;height:46px;background:var(--red);color:var(--white);font-size:15px;display:flex;align-items:center;justify-content:center}

/* content */
.welcome{left:169px;top:626px;font-size:32px;font-weight:900;color:var(--red)}
.body-copy{font-size:15px;line-height:23.2px;width:590px}
.topics{top:956px;list-style:none;font-size:16px;line-height:33.5px}
.topics li{display:flex;align-items:center;gap:8px}
.topics svg{width:10px;height:14px}
.section-title{font-size:24px;color:var(--navy)}
.screen{top:1444px;height:213px;width:278px;background:linear-gradient(180deg,#e8e8e8 0%,#f6f6f6 12%,#ffffff 100%);border:1px solid #d4d4d4}
.video{width:569px;height:312px}
.play{position:absolute;left:50%;top:50%;width:62px;height:62px;margin:-31px 0 0 -31px;border-radius:50%;background:var(--white);display:flex;align-items:center;justify-content:center}

/* sidebar */
.sample-box{left:800px;top:602px;width:252px;height:92px;background:linear-gradient(180deg,#2a5b97,#123d70);color:var(--white);text-align:center;font-family:"Lato",sans-serif;font-weight:700;padding-top:22px}
.sample-box .small{font-size:17px}
.sample-box .big{font-size:21px}
.rule{left:798px;width:254px;height:2px;background:var(--red)}
.side-title{font-size:21px;color:#1a1a1a}
.course-name{left:810px;width:240px;font-family:"Lato",sans-serif;font-weight:700;font-size:15px;line-height:22px;color:var(--link);text-transform:uppercase}
.btn-click{left:810px;width:126px;height:36px;border:2px solid var(--red);color:var(--red);font-family:"Lato",sans-serif;font-size:15px;display:flex;align-items:center;justify-content:center}
.post{left:805px;width:240px;font-family:"Lato",sans-serif;font-size:15px;line-height:16px;color:var(--link)}

/* footer */
.site-footer{left:0;top:2554px;width:1200px;height:337px;background:var(--navy-deep)}
.footer-mark{left:166px;top:2694px;font-family:"Lato",sans-serif;font-weight:700;font-size:22px;color:#3c5e8c}
.foot-col{top:2620px;font-family:"Lato",sans-serif;color:var(--white)}
.foot-col h3{font-size:20px;font-weight:700;text-transform:uppercase;margin-bottom:18px}
.foot-col a{display:block;font-size:15.5px;line-height:28.7px;color:#d7dfea;text-decoration:none;padding-left:3px}
.social a{display:flex;align-items:center;gap:14px;line-height:36px}
.social span.ico{width:16px;height:16px;border-radius:50%;background:#d7dfea}
.bottom-bar{left:0;top:2891px;width:1200px;height:70px;background:var(--navy-darker);color:#b9c4d4;font-family:"Lato",sans-serif;font-size:15px;text-align:center;padding-top:22px}
</style>
</head>
<body>

<header class="abs site-header">
  <div class="abs brand"><span class="brand-dot"></span>VERDANA CREST</div>
  <nav class="abs main-nav"><span>ABOUT US</span><span>COURSES</span><span>WORKSHEET</span><span>QUIZZES</span><span>BLOGS</span><span>CONTACT</span></nav>
</header>

<section class="abs hero" role="img" aria-label="Photo of a smiling woman writing at a desk beside a laptop"></section>
<h1 class="abs heading hero-title">Verdana Crest Learning System</h1>
<p class="abs hero-sub">Get Your Bearings. Plan Your Course.</p>
<div class="abs heading btn-launch">Ready to Launch</div>

<h2 class="abs heading welcome">Welcome to Verdana Crest!</h2>
<p class="abs body-copy" style="left:168px;top:689px">Verdana Crest, our professional online training platform, is an online learning application geared toward corporate customers, allowing their employees to identify and cultivate new skills that will be valuable in both their professional and personal lives. Named after a guiding star, Verdana Crest can help your people get their bearings for where they’re headed, and then help them plan a course to get there.</p>
<p class="abs body-copy" style="left:168px;top:864px">Concentrating on subjects that are useful to each student not only in the business world but also in life as well, Verdana Crest offers courses on various topics including:</p>

<ul class="abs topics" style="left:172px">
  <li><svg viewBox="0 0 10 14"><path d="M2 1l6 6-6 6" fill="none" stroke="#1d4a82" stroke-width="2.6"/></svg>Become a Better Listener</li>
  <li><svg viewBox="0 0 10 14"><path d="M2 1l6 6-6 6" fill="none" stroke="#1d4a82" stroke-width="2.6"/></svg>Proactive Decision-Making</li>
  <li><svg viewBox="0 0 10 14"><path d="M2 1l6 6-6 6" fill="none" stroke="#1d4a82" stroke-width="2.6"/></svg>Improving Self-Awareness</li>
  <li><svg viewBox="0 0 10 14"><path d="M2 1l6 6-6 6" fill="none" stroke="#1d4a82" stroke-width="2.6"/></svg>The Power of Priorities</li>
</ul>
<ul class="abs topics" style="left:448px">
  <li><svg viewBox="0 0 10 14"><path d="M2 1l6 6-6 6" fill="none" stroke="#1d4a82" stroke-width="2.6"/></svg>Mastering Habits</li>
  <li><svg viewBox="0 0 10 14"><path d="M2 1l6 6-6 6" fill="none" stroke="#1d4a82" stroke-width="2.6"/></svg>Managing a To-Do List</li>
  <li><svg viewBox="0 0 10 14"><path d="M2 1l6 6-6 6" fill="none" stroke="#1d4a82" stroke-width="2.6"/></svg>Perfection: The Enemy of Progress</li>
</ul>

<h2 class="abs heading section-title" style="left:156px;top:1139px">Different Learning Styles</h2>
<p class="abs body-copy" style="left:157px;top:1187px;width:595px">Verdana Crest realizes that different people learn in different ways, so we strive to accommodate that. The courses within Verdana Crest include various methods of information dissemination in order to allow for different learning styles: some reading, some video, some reflections, some group activities, and some journaling. Each course includes a brief quiz to ensure you’ve absorbed the important information. And, if your organization chooses to work through these courses together as a group, that will further enhance your team’s learning experience.</p>

<h2 class="abs heading section-title" style="left:156px;top:1394px">Sample Screens</h2>
<div class="abs screen" style="left:159px" role="img" aria-label="Screenshot of a course lesson page"></div>
<div class="abs screen" style="left:456px" role="img" aria-label="Screenshot of a course quiz page"></div>

<h2 class="abs heading section-title" style="left:167px;top:1714px">Overview Video</h2>
<div class="abs video" style="left:167px;top:1764px;background:linear-gradient(135deg,#6f7378,#4a4f58 55%,#2f3440)" role="img" aria-label="Video still of a woman in glasses working on a laptop"><span class="play"><svg width="20" height="22" viewBox="0 0 20 22"><path d="M2 1l17 10L2 21z" fill="#111"/></svg></span></div>
<div class="abs video" style="left:168px;top:2132px;background:linear-gradient(135deg,#a07a52,#7a5c40 55%,#4f3e30)" role="img" aria-label="Video still of hands typing on a laptop on a wooden table"><span class="play"><svg width="20" height="22" viewBox="0 0 20 22"><path d="M2 1l17 10L2 21z" fill="#111"/></svg></span></div>

<aside>
  <div class="abs sample-box"><div class="small">SAMPLE OUR</div><div class="big">SKILL COURSES</div></div>
  <div class="abs rule" style="top:717px"></div>
  <h3 class="abs heading side-title" style="left:810px;top:743px">Our Courses</h3>
  <div class="abs course-name" style="top:793px">Aravida non tristique vel<br>tellus pellentes</div>
  <div class="abs btn-click" style="top:843px">CLICK HERE</div>
  <div class="abs course-name" style="top:904px">Duis sed tellus et tortor<br>vestibulum gravid</div>
  <div class="abs btn-click" style="top:956px">CLICK HERE</div>
  <div class="abs course-name" style="top:1017px;line-height:26px">Proin nulla arcu<br>luctus dictum</div>
  <div class="abs btn-click" style="top:1076px">CLICK HERE</div>
  <div class="abs course-name" style="top:1143px;line-height:26px">Maecenas aliquet vel<br>turpis mauris</div>
  <div class="abs btn-click" style="top:1204px">CLICK HERE</div>
  <div class="abs rule" style="top:1273px"></div>
  <h3 class="abs heading side-title" style="left:805px;top:1302px">Recent Posts</h3>
  <div class="abs post" style="top:1346px">Aetus vitae adipiscing semper<br>mauris ipsum iaculis</div>
  <div class="abs post" style="top:1396px">Elit congue gravida elit mi egestas<br>orci Curabitur pede</div>
  <div class="abs post" style="top:1446px">Maecenas aliquet velit vel turpis</div>
  <div class="abs post" style="top:1481px">Pauris neque metus malesuada nec<br>ultricies sit amet porttitor</div>
  <div class="abs post" style="top:1531px">Mattis enim In massa libero</div>
  <div class="abs post" style="top:1566px">Jnterdum nec interdum vel blandit<br>sed nulla In ullamcorper est</div>
  <div class="abs post" style="top:1616px">Eget tempor cursus neque mi</div>
</aside>

<footer class="abs site-footer"></footer>
<div class="abs footer-mark">VERDANA CREST</div>
<div class="abs foot-col" style="left:386px"><h3>Quick Links</h3><a>Home</a><a>About us</a><a>Our Courses</a><a>Worksheet</a><a>Quizzes</a></div>
<div class="abs foot-col" style="left:566px"><h3>Courses</h3><a>Lorem ipsum</a><a>Dolor sit</a><a>Amet consecte</a><a>Tuer adipiscing</a><a>Nam cursus</a></div>
<div class="abs foot-col" style="left:735px"><h3>Resources</h3><a>Testimonials</a><a>Blogs</a><a>Career</a><a>FAQ</a><a>Contact Us</a></div>
<div class="abs foot-col social" style="left:887px"><h3>Social Media</h3><a><span class="ico"></span>Friendspace</a><a><span class="ico"></span>Chirpline</a><a><span class="ico"></span>Workrings</a><a><span class="ico"></span>Snapgallery</a></div>
<div class="abs bottom-bar">© 2019 Company Name &nbsp;All right reserved</div>

</body>
</html>
```